Improved Business Card, Government Contracting

We are looking to update the design of our business cards. We would like to create a template that can be used for future employees and easy to update.

Halvorsen Advisory Partners, LLC is a Service Disabled Veteran Owned Small Business with headquarters located in Leavenworth, KS. Our current website is www.hvadpt.com. We have contracts in KS and VA with expansion opportunities in various other states. Our primary line of work is within government contracting and providing consulting services to various organizations within the Bureau of Civic Readiness. We would like to project a professional image of our company that is consistent with the industry. Provided are previous versions of our business card template that shows our logo as well. We would like to make sure the information on the cards are easily noticeable .

Target Market(s)

Government Officials
Fellow Small Business Contractors
Large Business Contractors (ex. TQLB, Pellwick Darrow, Fenwey Marsh Colquitt)

Industry/Entity Type

Business

Contact Information for Business Card

Dale Forsyth
Office Manager
Halvorsen Advisory Partners
Ph: 555.204.7716
Email: d.forsyth@hvadpt.us
www.hvadpt.com

Requirements
Must have
• The business mailing address is:
• 48730 212th Crescent
• Leavenworth, KS 66091
Nice to have
• Embossed lettering

```html
<!DOCTYPE html>
<html lang="en">
<head>
<meta charset="utf-8">
<title>Halvorsen Advisory Partners – Business Card</title>
<link rel="stylesheet" href="https://fonts.googleapis.com/css2?family=Nunito+Sans:ital,wght@0,400;0,700;0,800;1,400&display=swap">
<style>
  :root {
    --brand-blue: #3d5ca8;
    --brand-gold: #fcc40c;
    --paper: #ffffff;
    --ink-light: #ffffff;
  }
  html, body {
    margin: 0;
    padding: 0;
    width: 1200px;
    height: 683px;
    overflow: hidden;
    background: var(--paper);
  }
  .card {
    position: relative;
    width: 1200px;
    height: 683px;
    overflow: hidden;
    background: var(--paper);
    font-family: "Nunito Sans", Arial, sans-serif;
  }
  .card-backdrop {
    position: absolute;
    inset: 0;
    width: 1200px;
    height: 683px;
  }
  .panel-gold { fill: var(--brand-gold); }
  .panel-blue { fill: var(--brand-blue); }

  .company-name {
    position: absolute;
    left: 0;
    top: 190px;
    width: 1200px;
    margin: 0;
    text-align: center;
    font-size: 48px;
    font-weight: 700;
    letter-spacing: 1px;
    line-height: 1.2;
    color: var(--brand-blue);
  }

  .person {
    position: absolute;
    left: 78px;
    top: 406px;
    color: var(--brand-blue);
  }
  .person-name {
    margin: 0;
    font-size: 44px;
    font-weight: 800;
    line-height: 1.1;
  }
  .person-title {
    margin: 4px 0 0;
    font-size: 31px;
    font-style: italic;
    font-weight: 400;
    line-height: 1.2;
  }

  .contact {
    position: absolute;
    right: 58px;
    top: 412px;
    margin: 0;
    padding: 0;
    list-style: none;
    text-align: right;
    color: var(--ink-light);
    font-size: 32px;
    line-height: 48px;
  }
  .contact-label { font-weight: 800; }

  .mailing-address {
    position: absolute;
    right: 58px;
    top: 522px;
    margin: 0;
    text-align: right;
    color: var(--ink-light);
    font-size: 22px;
    font-style: normal;
    line-height: 1.2;
  }

  .website {
    position: absolute;
    right: 58px;
    top: 576px;
    margin: 0;
    color: var(--ink-light);
    font-size: 32px;
    font-weight: 800;
    line-height: 1.2;
    letter-spacing: 0.5px;
  }
</style>
</head>
<body>
  <main class="card">
    <svg class="card-backdrop" viewBox="0 0 1200 683" aria-hidden="true">
      <polygon class="panel-gold" points="0,190 600,450 75,683 0,683"/>
      <polygon class="panel-blue" points="1200,195 1200,683 75,683 600,450"/>
    </svg>

    <h1 class="company-name">Halvorsen Advisory Partners</h1>

    <section class="person">
      <p class="person-name">Dale Forsyth</p>
      <p class="person-title">Office Manager</p>
    </section>

    <ul class="contact">
      <li><span class="contact-label">P:</span> 555.204.7716</li>
      <li><span class="contact-label">E:</span> d.forsyth@hvadpt.us</li>
    </ul>

    <address class="mailing-address">48730 212th Crescent, Leavenworth, KS 66091</address>

    <p class="website">www.hvadpt.com</p>
  </main>
</body>
</html>
```